BMR Going Cashless

Hello,
We are a medical office looking to get a flyer created to promote to our patients we will be going "Cashless." Our tagline will be "Cash-Less is Stress-Less"

"Starting in July, to offer you the fastest and most convenient service, we are transitioning to a cashless system. You can now enjoy faster checkout times and greater security with card and contactless payments. More info to come."

I've added two other flyers as sample designs we've used.

Please include logo, addresses, website, phone number

Files to include jpeg, png, pdf (under 5mb), Facebook and Instagram sizing.

Thank you,
Lowen

```html
<!DOCTYPE html>
<html lang="en">
<head>
<meta charset="utf-8">
<title>BMR Going Cashless</title>
<link rel="stylesheet" href="https://fonts.googleapis.com/css2?family=Bebas+Neue&family=Montserrat:ital,wght@0,400;0,500;0,600;0,700;0,800;1,800&family=Poppins:wght@400&family=Yellowtail&display=block">
<style>
:root{
  --board:#b3b3b3;
  --dark:#2a2a2a;
  --teal:#55c3a6;
  --orange:#f07a3f;
  --white:#ffffff;
  --ink:#2b2b2b;
}
*{margin:0;padding:0;box-sizing:border-box}
html,body{width:1200px;height:2749px;overflow:hidden}
body{background:var(--board);position:relative;font-family:"Montserrat",sans-serif}
.size-label{position:absolute;left:0;width:1200px;text-align:center;font-family:"Poppins",sans-serif;font-size:43px;color:#1e1e1e;letter-spacing:1px}
.abs{position:absolute;z-index:2}
.artboard{position:absolute;overflow:hidden;box-shadow:0 12px 18px rgba(0,0,0,.35)}
.square{left:206px;top:143px;width:788px;height:788px;background:radial-gradient(circle at 78% 40%,#5a5a5a 0%,#333 45%,var(--dark) 75%)}
.story{left:221px;top:1166px;width:759px;height:1348px;background:radial-gradient(circle at 55% 35%,#4e4e4e 0%,#333 45%,var(--dark) 75%)}
.bg-shape{position:absolute;left:0;top:0;z-index:0}
.script{font-family:"Yellowtail",cursive;line-height:1;white-space:nowrap}
.headline{font-family:"Bebas Neue",sans-serif;line-height:1;white-space:nowrap}
.badge{background:var(--orange);color:var(--white);border:2px solid var(--white);border-radius:8px;font-weight:700;text-align:center;letter-spacing:6px;line-height:1}
.month{color:var(--white);font-weight:800;line-height:1;letter-spacing:1px}
.body-copy{color:var(--ink);font-weight:500;line-height:1.15}
.terminal{position:absolute;z-index:1;border-radius:40px 40px 60px 60px;background:linear-gradient(160deg,#e9e6df 0%,#e9e6df 12%,#3d4350 13%,#4b5262 40%,#2c313b 100%);transform:rotate(12deg)}
.spaced{color:var(--white);font-weight:700;letter-spacing:4px;white-space:nowrap}
.brand{display:flex;align-items:center;gap:10px;color:var(--orange);font-weight:800;line-height:1;white-space:nowrap}
.brand-dot{border-radius:50%;background:var(--teal)}
.office-title{color:var(--teal);font-weight:700;white-space:nowrap}
.office-addr{color:var(--white);font-weight:500;line-height:1.2}
.web-bar{background:var(--orange);color:var(--white);letter-spacing:3px;white-space:nowrap}
.web-bar b{font-weight:800}
.phone{font-weight:800;white-space:nowrap;line-height:1}
.square .office{position:absolute;z-index:2;top:660px;width:150px;text-align:center}
.square .office-title{font-size:13px;margin-top:4px}
.square .office-addr{font-size:10px;margin-top:2px}
.square .sep{position:absolute;top:645px;height:84px;border-left:1.5px dashed #bbb}
.story .office{position:absolute;z-index:2;top:1137px;width:224px;height:117px;background:var(--dark);border-radius:6px;text-align:center;padding-top:33px}
.story .office svg{position:absolute;left:100px;top:-10px}
.story .office-title{font-size:20px}
.story .office-addr{font-size:16px;margin-top:4px;font-weight:400}
.benefits{list-style:none}
.benefits li{position:relative;padding-left:25px;color:var(--ink);font-size:22px;font-weight:500;margin-bottom:10px;line-height:1.15}
.benefits li::before{content:"";position:absolute;left:0;top:7px;width:13px;height:13px;border-radius:50%;background:var(--orange)}
</style>
</head>
<body>

<section class="artboard square">
  <svg class="bg-shape" width="788" height="788" viewBox="0 0 788 788"><path d="M0 0H578C565 250 400 470 200 470C110 470 40 455 0 438Z" fill="var(--teal)"/></svg>

  <div class="terminal" role="img" aria-label="Photo of a card payment terminal with receipt paper" style="left:480px;top:95px;width:225px;height:420px;transform:rotate(14deg)"></div>

  <div class="abs script" style="left:30px;top:50px;font-size:112px;color:var(--ink)">Cash-Less</div>
  <div class="abs headline" style="left:37px;top:156px;font-size:88px;color:var(--white)">IS STRESS-LESS</div>
  <div class="abs badge" style="left:39px;top:250px;width:192px;height:35px;font-size:25px;padding-top:4px">STARTING</div>
  <div class="abs month" style="left:39px;top:294px;font-size:63px">IN JULY</div>
  <p class="abs body-copy" style="left:40px;top:363px;width:300px;font-size:16.5px">To offer you the fastest and most convenient service, we are transitioning to a cashless system</p>

  <p class="abs" style="left:44px;top:492px;font-size:20px;color:var(--white);line-height:1.2">Now you can enjoy<br><span style="color:var(--teal);font-weight:700">faster checkout times and<br>greater security with card and</span></p>
  <div class="abs" style="left:43px;top:565px;font-size:30px;font-style:italic;font-weight:800;color:var(--orange);white-space:nowrap">CONTACTLESS PAYMENTS</div>
  <div class="abs spaced" style="left:44px;top:613px;font-size:13px">MORE INFO TO COME....</div>

  <div class="abs brand" style="right:42px;top:570px;font-size:40px"><span class="brand-dot" style="width:26px;height:26px"></span>BMR</div>

  <div class="abs" style="left:42px;top:641px;width:746px;border-top:1.5px solid #9a9a9a"></div>

  <div class="office" style="left:25px">
    <svg width="20" height="20" viewBox="0 0 20 20"><circle cx="10" cy="10" r="10" fill="var(--orange)"/><path d="M10 4a4 4 0 0 0-4 4c0 3 4 7 4 7s4-4 4-7a4 4 0 0 0-4-4zm0 5.5a1.5 1.5 0 1 1 0-3 1.5 1.5 0 0 1 0 3z" fill="#fff"/></svg>
    <div class="office-title">Northgate Office</div>
    <div class="office-addr">212 Maple Grove Dr. Suite 140 Northgate, MD 20000</div>
  </div>
  <div class="sep" style="left:168px"></div>
  <div class="office" style="left:175px">
    <svg width="20" height="20" viewBox="0 0 20 20"><circle cx="10" cy="10" r="10" fill="var(--orange)"/><path d="M10 4a4 4 0 0 0-4 4c0 3 4 7 4 7s4-4 4-7a4 4 0 0 0-4-4zm0 5.5a1.5 1.5 0 1 1 0-3 1.5 1.5 0 0 1 0 3z" fill="#fff"/></svg>
    <div class="office-title">Riverside Office</div>
    <div class="office-addr">58 Clinic Way<br>Riverside, WV 25000</div>
  </div>
  <div class="sep" style="left:331px"></div>
  <div class="office" style="left:330px">
    <svg width="20" height="20" viewBox="0 0 20 20"><circle cx="10" cy="10" r="10" fill="var(--orange)"/><path d="M10 4a4 4 0 0 0-4 4c0 3 4 7 4 7s4-4 4-7a4 4 0 0 0-4-4zm0 5.5a1.5 1.5 0 1 1 0-3 1.5 1.5 0 0 1 0 3z" fill="#fff"/></svg>
    <div class="office-title">Hillcrest Office</div>
    <div class="office-addr">760 Oakridge Blvd. Suite 201 Hillcrest, MD 20001</div>
  </div>

  <div class="abs" style="left:512px;top:650px;font-size:16px;font-weight:700;letter-spacing:4.5px;color:var(--teal);white-space:nowrap">CONTACT US TODAY</div>
  <svg class="abs" style="left:510px;top:680px" width="30" height="30" viewBox="0 0 30 30"><circle cx="15" cy="15" r="15" fill="var(--orange)"/><path d="M10 8c1-1 2-1 2.5 0l1.5 3c.3.6 0 1.2-.5 1.6l-1 .8c.8 1.8 2.2 3.2 4 4l.8-1c.4-.5 1-.8 1.6-.5l3 1.5c1 .5 1 1.5 0 2.5-1.5 1.5-3.5 1.5-6 0-2.8-1.7-5-4-6.5-6.7-1.3-2.4-1-4.2.6-5.2z" fill="#fff"/></svg>
  <div class="abs phone" style="left:547px;top:681px;font-size:29px;color:var(--white)">(877) 555-0148</div>
  <div class="abs web-bar" style="left:508px;top:717px;width:280px;height:26px;font-size:15px;padding:4px 0 0 16px">www.<b>stridewellcare</b>.com</div>
</section>
<div class="size-label" style="top:990px">1080 X 1080</div>

<section class="artboard story">
  <svg class="bg-shape" width="759" height="1348" viewBox="0 0 759 1348"><path d="M0 731C200 640 600 610 759 720V1348H0Z" fill="var(--teal)"/></svg>

  <div class="terminal" role="img" aria-label="Photo of a card payment terminal with receipt paper" style="left:290px;top:420px;width:255px;height:460px"></div>

  <div class="abs brand" style="left:0;width:759px;justify-content:center;top:48px;font-size:54px"><span class="brand-dot" style="width:32px;height:32px"></span>BMR</div>

  <div class="abs script" style="left:0;width:759px;text-align:center;top:125px;font-size:160px;color:var(--teal)">Cash-Less</div>
  <div class="abs headline" style="left:0;width:759px;text-align:center;top:280px;font-size:132px;color:var(--orange)">IS STRESS-LESS</div>

  <div class="abs badge" style="left:38px;top:896px;width:215px;height:36px;font-size:27px;padding-top:3px">STARTING</div>
  <div class="abs month" style="left:35px;top:946px;font-size:72px">IN JULY</div>
  <p class="abs body-copy" style="left:36px;top:1025px;width:320px;font-size:19px;font-weight:400">To offer you the fastest and most convenient service, we are transitioning to a cashless system</p>

  <div class="abs" style="left:380px;top:897px;height:192px;border-left:2px dotted #3d6a5e"></div>

  <div class="abs" style="left:405px;top:893px;font-size:28px;font-weight:700;color:var(--white);white-space:nowrap">YOU CAN <span style="color:var(--orange)">NOW ENJOY</span></div>
  <ul class="abs benefits" style="left:411px;top:950px">
    <li>Faster checkout times</li>
    <li>Greater security with card</li>
    <li>Contactless payments</li>
  </ul>
  <div class="abs spaced" style="left:410px;top:1076px;font-size:14px;letter-spacing:5px">MORE INFO TO COME....</div>

  <div class="office" style="left:37px">
    <svg width="26" height="26" viewBox="0 0 20 20"><circle cx="10" cy="10" r="10" fill="var(--orange)"/><path d="M10 4a4 4 0 0 0-4 4c0 3 4 7 4 7s4-4 4-7a4 4 0 0 0-4-4zm0 5.5a1.5 1.5 0 1 1 0-3 1.5 1.5 0 0 1 0 3z" fill="#fff"/></svg>
    <div class="office-title">Northgate Office</div>
    <div class="office-addr">212 Maple Grove<br>Dr. Suite 140 Northgate,<br>MD 20000</div>
  </div>
  <div class="office" style="left:268px">
    <svg width="26" height="26" viewBox="0 0 20 20"><circle cx="10" cy="10" r="10" fill="var(--orange)"/><path d="M10 4a4 4 0 0 0-4 4c0 3 4 7 4 7s4-4 4-7a4 4 0 0 0-4-4zm0 5.5a1.5 1.5 0 1 1 0-3 1.5 1.5 0 0 1 0 3z" fill="#fff"/></svg>
    <div class="office-title">Riverside Office</div>
    <div class="office-addr">58 Clinic Way<br>Riverside, WV 25000</div>
  </div>
  <div class="office" style="left:499px">
    <svg width="26" height="26" viewBox="0 0 20 20"><circle cx="10" cy="10" r="10" fill="var(--orange)"/><path d="M10 4a4 4 0 0 0-4 4c0 3 4 7 4 7s4-4 4-7a4 4 0 0 0-4-4zm0 5.5a1.5 1.5 0 1 1 0-3 1.5 1.5 0 0 1 0 3z" fill="#fff"/></svg>
    <div class="office-title">Hillcrest Office</div>
    <div class="office-addr">760 Oakridge<br>Blvd. Suite 201 Hillcrest,<br>MD 20001</div>
  </div>

  <svg class="abs" style="left:39px;top:1272px" width="40" height="40" viewBox="0 0 30 30"><circle cx="15" cy="15" r="15" fill="var(--orange)"/><circle cx="15" cy="15" r="12.5" fill="none" stroke="#fff" stroke-width="1.2"/><path d="M10 8c1-1 2-1 2.5 0l1.5 3c.3.6 0 1.2-.5 1.6l-1 .8c.8 1.8 2.2 3.2 4 4l.8-1c.4-.5 1-.8 1.6-.5l3 1.5c1 .5 1 1.5 0 2.5-1.5 1.5-3.5 1.5-6 0-2.8-1.7-5-4-6.5-6.7-1.3-2.4-1-4.2.6-5.2z" fill="#fff"/></svg>
  <div class="abs phone" style="left:90px;top:1271px;font-size:38px;color:var(--ink)">(877) 555-0148</div>
  <div class="abs web-bar" style="left:387px;top:1263px;width:372px;height:36px;border:2px solid var(--white);border-right:none;border-radius:18px 0 0 18px;font-size:21px;padding:4px 0 0 20px">www.<b>stridewellcare</b>.com</div>
</section>
<div class="size-label" style="top:2574px">1920 X 1080</div>

</body>
</html>
```